Design and Renovation Company Luxury Business Card

I want to create a luxury business card for a Design and Renovation Firm . We will use our current logo. The company name is 528BUILDA. We do not want anything standard. We need a very unique concept.
Please see uploaded inspiration. I really like the textured paper option. I would like the card to be thick with debossing, and/or embossing options. The logo has orange in it but I would like to see the card with and without the orange. I think the orange may make the company feel less high-end. The goal is to elevate the logo not match its vibe per se of the logo. We want something very unique, not standard at all!
I would like a space for :
Logo,
Name,
Position,
Email,
Office number,
Website Address,
Business Address,
Thank you!
Have fun!
Target Market(s)
Home owners Age 35 +
Industry/Entity Type
Design and Renovation
Contact Information for Business Card
Logo, Name, Position, Email, Office number, Website Address, Business Address,.
Colors
Designer to choose colors to be used in the design.
Requirements
Must have
- A luxury designer feel. Must be black or dark grey but open to other luxury ideas.
Nice to have
- Gold, silver, black embossing or debossing. Textured paper design.
Should not have
- A cheap look and feel.

```html
<!DOCTYPE html>
<html lang="en">
<head>
<meta charset="utf-8">
<title>528BUILDA Business Card</title>
<link href="https://fonts.googleapis.com/css2?family=Montserrat:wght@400;500;600&display=swap" rel="stylesheet">
<style>
  :root {
    --backdrop: #141414;
    --card: #2a2a2a;
    --card-edge: #1f1f1f;
    --silver: #a9a9a9;
    --silver-dim: #8a8a8a;
    --ink-light: #f2f2f2;
    --accent: #f0a020;
  }
  * { margin: 0; padding: 0; box-sizing: border-box; }
  html, body {
    width: 1200px;
    height: 1063px;
    overflow: hidden;
    background: var(--backdrop);
    font-family: "Montserrat", sans-serif;
  }
  .sheet {
    width: 1200px;
    height: 1063px;
    display: flex;
    flex-direction: column;
    align-items: center;
    justify-content: center;
    gap: 44px;
  }
  .card {
    position: relative;
    width: 800px;
    height: 457px;
    background: var(--card);
    border: 1px solid var(--card-edge);
    box-shadow: 0 14px 30px rgba(0,0,0,0.55);
  }
  /* Front */
  .brand {
    position: absolute;
    left: 50%;
    top: 50%;
    transform: translate(-50%, -50%);
    display: flex;
    flex-direction: column;
    align-items: flex-start;
  }
  .brand-row {
    display: flex;
    align-items: center;
    gap: 18px;
  }
  .brand-mark {
    width: 46px;
    height: 46px;
    background: var(--silver-dim);
  }
  .brand-name {
    font-weight: 500;
    font-size: 76px;
    line-height: 1;
    letter-spacing: 4px;
    color: var(--silver);
  }
  .brand-tagline {
    margin-top: 8px;
    margin-left: 66px;
    font-weight: 500;
    font-size: 19px;
    letter-spacing: 5px;
    color: var(--silver);
  }
  /* Back */
  .contact {
    position: absolute;
    left: 80px;
    top: 170px;
    color: var(--ink-light);
  }
  .contact-name {
    font-weight: 500;
    font-size: 30px;
    letter-spacing: 2px;
    text-transform: uppercase;
  }
  .contact-role {
    font-weight: 600;
    font-size: 15px;
    margin-top: 2px;
  }
  .contact-address {
    margin-top: 24px;
    font-size: 19px;
    line-height: 1.35;
  }
  .contact-lines {
    margin-top: 16px;
    list-style: none;
    font-size: 19px;
    line-height: 1.35;
  }
  .contact-lines li {
    display: flex;
    align-items: center;
    gap: 10px;
  }
  .contact-lines svg { width: 16px; height: 16px; flex: none; }
  .back-mark {
    position: absolute;
    right: 70px;
    top: 130px;
    width: 76px;
    height: 76px;
    background: var(--accent);
  }
</style>
</head>
<body>
<main class="sheet">
  <section class="card card-front" aria-label="Card front">
    <div class="brand">
      <div class="brand-row">
        <span class="brand-mark"></span>
        <span class="brand-name">528BUILDA</span>
      </div>
      <span class="brand-tagline">Design and Renovation Firm</span>
    </div>
  </section>

  <section class="card card-back" aria-label="Card back">
    <div class="contact">
      <h1 class="contact-name">Daniel Reyes</h1>
      <p class="contact-role">President</p>
      <p class="contact-address">4120 Juniper Court<br>Halden, Canada 58210</p>
      <ul class="contact-lines">
        <li>
          <svg viewBox="0 0 16 16" aria-hidden="true"><path d="M4 1.5l2.5 3-1.5 1.8c.8 1.7 2 2.9 3.7 3.7L10.5 8.5l3 2.5-1.5 3C7 13.5 2.5 9 2 4z" fill="#f2f2f2"/></svg>
          555-218-6042
        </li>
        <li>
          <svg viewBox="0 0 16 16" aria-hidden="true"><rect x="3" y="1" width="9" height="14" rx="1.5" fill="none" stroke="#f2f2f2" stroke-width="1.5"/><circle cx="7.5" cy="12.5" r="0.9" fill="#f2f2f2"/></svg>
          info@528builda.com
        </li>
        <li>
          <svg viewBox="0 0 16 16" aria-hidden="true"><rect x="1" y="3" width="14" height="10" fill="#f2f2f2"/><path d="M1 3l7 6 7-6" fill="none" stroke="#2a2a2a" stroke-width="1.3"/></svg>
          www.528builda.com
        </li>
      </ul>
    </div>
    <span class="back-mark"></span>
  </section>
</main>
</body>
</html>
```